Thornbury Spa

We are a large Miami Beach spa and salon. I am still building our website but you can use it as a resource to gain a better understanding of who we are ....www.velloraspa-studio.com.

We offer a comprehensive list of services in hair, nails, massage, skin care, tanning, spray tanning and waxing and we offer high quality products for skin care, tanning and hair. We are open 7 days.

We would like to see a clean and simple menu that looks a lot like the one from "The Spa at Larkwood." In particular, we have a copy of a menu from their West Hollywood, CA location that is just beautiful. In the uploaded content you will see a sampling of that menu. We would like to see greys, blacks, silvers, whites and warm colors like reds and oranges. We specifically attempt to remain gender neutral so that we don't attract only girls (with pink colors and flowers etc). The final design should convey a simple, clean, friendly environment and the final product should be sized such that it is 1.) portable and 2.) inexpensive to print. We will be running thousands of these at a time so cost of printing is a consideration.

The booklet consists of two parts: one part is the standard menu with descriptions of services and products and photos etc (think of this as the sales piece that convinces a potential customer to visit) and will be stapled together like you would expect a small menu to be and should resemble the Larkwood menu. The prices should not be included in this part of the booklet that will be printed and stapled. The other part is a single insert and is removable and replaceable. I want this removable insert placed in the last page of the book in a folder pocket or something else that you can think of so that when it's time to change prices here that I am not throwing away all of the booklets....I am only replacing the inserts at the end of the menu booklet. Please design this single page insert so that should a customer remove it from the booklet and keep it, that it stands alone with our name, logo, website and phone number. This page can and probably will have to be 2 sided.

At the back of the booklet, I also want the polices to be printed in one page (think fine print in any sort of business dealing.)

With regard to the look and feel slider of economical v upmarket...we definitely want to convey we deliver upmarket services at reasonable prices. Think, world class services and products at reasonable, everyday prices.

With regard to the uploaded files:
I uploaded both EPS and TIF formats. The colors in those files are not the palette we want at all. The colors we want use for the circular logo must match the standard colors as depicted in the uploaded file "Thornburytanrooms"

Target Market(s)

The target market is the average 20-35 year old in Miami Beach that cares about their appearance. The range of clientele is quite diverse.

Industry/Entity Type

Environment

Requirements
Must have
• It must have elegant and simple photographs that relate to the services being offered. We are selling a service set and an environment...so this menu should be reflect that goal. The logo should be repeated often throughout the book but in subtle ways.

Stock photos are fine as long as they don't seem obviously stock.

Should not have
• Nothing buddha like. Nothing themed. It should be all inclusive and not seek to identify with any particular group or gender.

Nothing that fits the stereotype of "Miami Beach." We want to represent ourselves in the same category as the best spas in the world because we moving everything we do in that direction. Think class!

```html
<!DOCTYPE html>
<html lang="en">
<head>
<meta charset="utf-8">
<title>Thornbury Spa — Massage Menu</title>
<link href="https://fonts.googleapis.com/css2?family=Nunito+Sans:wght@400;600&family=Raleway:wght@200;300;400&display=swap" rel="stylesheet">
<style>
  :root {
    --charcoal-edge: #1f1f21;
    --charcoal-mid: #3b3b3d;
    --heading-bar: #8e8f93;
    --heading-text: #f2f2f2;
    --body-text: #e9e9ea;
    --wine: #7b2f46;
    --logo-grey: #c9cacd;
    --title-white: rgba(255, 255, 255, 0.88);
  }
  * { margin: 0; padding: 0; box-sizing: border-box; }
  html, body { width: 1200px; height: 423px; overflow: hidden; background: var(--charcoal-edge); }
  .spread {
    position: relative;
    width: 1200px; height: 423px; overflow: hidden;
    background: radial-gradient(ellipse 70% 90% at 45% 50%, var(--charcoal-mid) 0%, #2c2c2e 55%, var(--charcoal-edge) 100%);
    font-family: "Nunito Sans", sans-serif;
    color: var(--body-text);
  }
  .service { position: absolute; width: 260px; }
  .service h2 {
    width: 178px; height: 11px;
    background: var(--heading-bar);
    font-family: "Raleway", sans-serif;
    font-weight: 400; font-size: 9.5px; letter-spacing: 1.4px;
    line-height: 11px; text-align: center; color: var(--heading-text);
    margin-bottom: 12px;
  }
  .service p {
    font-size: 7.5px; line-height: 11.6px; text-align: justify;
  }
  .shiatsu { left: 36px; top: 94px; }
  .aromatherapy { left: 36px; top: 282px; }
  .reflexology { left: 306px; top: 94px; }
  .deep-tissue { left: 306px; top: 238px; }
  .brand {
    position: absolute; left: 648px; top: 86px; width: 80px;
    text-align: center;
  }
  .brand-dot {
    display: block; width: 20px; height: 20px; margin: 0 auto 10px;
    border-radius: 50%; background: var(--logo-grey);
  }
  .brand-name {
    font-family: "Raleway", sans-serif; font-weight: 400;
    font-size: 9px; letter-spacing: 1.6px; line-height: 12px;
    color: var(--logo-grey); text-transform: uppercase;
  }
  .photo-panel { position: absolute; inset: 0; }
  .page-title {
    position: absolute; left: 1148px; top: 208px;
    transform: translate(-50%, -50%) rotate(90deg);
    font-family: "Raleway", sans-serif; font-weight: 200;
    font-size: 74px; letter-spacing: 6px; line-height: 1;
    color: var(--title-white); white-space: nowrap;
  }
</style>
</head>
<body>
<main class="spread">
  <section class="service shiatsu">
    <h2>SHIATSU</h2>
    <p>Shiatsu incorporates the theories of acupuncture that target the “chi,” or body energy, to move it along requisite energy pathways called meridians. It is an Asian form known to have an overall calming effect upon the body and can relieve muscle tension, alleviate stress and ease joint stiffness. It does not incorporate oils into the experience and as such, our Shiatsu clients can remain fully clothed for the experience if they so desire. Our therapists employ direct thumb, palm and forearm pressure on tight muscles to loosen them up; they also employ pressure with their knees to release pressure on large back muscles. The treatments typically are performed on a mat at floor level so our therapist can apply pressure against a hard surface and use his entire body to provide the pressure. The pressure and stretching techniques can realign the structure of the body by clearing energy blocks and moving stagnant energy out of tight places. The treatments tend to have an overall calming effect while relaxing the body.</p>
  </section>

  <section class="service aromatherapy">
    <h2>AROMATHERAPY</h2>
    <p>The sense of smell is the most primitive of senses. It is directly connected to the limbic system, from which emotions and memories originate. Our massage therapists will take the time to personalize your sensory journey that will either leave you either energized and refreshed or at peace and balanced- the choice is yours.</p>
  </section>

  <section class="service reflexology">
    <h2>REFLEXOLOGY</h2>
    <p>An ancient practice first noted in hieroglyphic references in a physician’s tomb at Saqqara in ancient Egypt, reflexology is an alternative health treatment that utilizes and encourages the body’s natural capacity to heal itself, by applying pressure to specific points on the feet, hands and ears called reflex points. Reflexology treatments are administered by applying direct physical pressure to the reflex points of the hands and feet with either finger, thumb or hand techniques. No oils or lotions are required in the treatment. Reflex points that exhibit blockages in energy flow normally feel bruised at best and painful at worst. Stimulating these reflexes properly can help many health problems in a natural way.</p>
  </section>

  <section class="service deep-tissue">
    <h2>DEEP TISSUE MASSAGE</h2>
    <p>A type of massage that aims to reduce tension and stress at the deeper tissues and structures of muscle and fascia through the slower application of deep pressure, especially in and around areas of tension and pain.</p>
  </section>

  <div class="brand">
    <span class="brand-dot"></span>
    <p class="brand-name">Thornbury<br>Spa</p>
  </div>

  <svg class="photo-panel" width="1200" height="423" viewBox="0 0 1200 423">
    <defs>
      <linearGradient id="room-tones" x1="0" y1="0" x2="1" y2="1">
        <stop offset="0" stop-color="#5a2c3c"/>
        <stop offset="0.35" stop-color="#8a4a3a"/>
        <stop offset="0.6" stop-color="#c98a55"/>
        <stop offset="1" stop-color="#e9d6c8"/>
      </linearGradient>
    </defs>
    <polygon class="wine-band" points="812,0 840,0 752,423 716,423" fill="var(--wine)"/>
    <polygon class="room-photo" points="836,0 1200,0 1200,423 748,423" fill="url(#room-tones)"
      role="img" aria-label="Photograph of a candlelit treatment room with two massage tables draped in white linens and scattered rose petals"/>
  </svg>

  <h1 class="page-title">MASSAGE</h1>
</main>
</body>
</html>
```